Automotive component supplier needs a business card design

We need a business card design for our company called Velran Global Components Ltd based in the UK. We are a supplier of interior and exterior components to premium car manufacturers such as Corvel Ashby, Hadley Fenn, Marquist and Tavarelli. We would like to see a modern business card design that uses the colour blue.

Target Market(s)

Premium automotive car manufacturers.

Industry/Entity Type

Automotive

Contact Information for Business Card

Company Name : Velran Global Components Limited
Address: 17 Marlow Yard, Upper Heath, Warwick, CV31 8QL, United Kingdom
Web Address : www.velrancomponents-example.co.uk

Font styles to use
Other font styles liked:
• Helvetica

Colors
3176b5
0255a3
85acd3
cfdeed
cee9f5
85cae6
34a6d7
0692cd
9bcb3c

Requirements
Must have
• Clear company logo and a mixture of blue colours.
Nice to have
• A high quality modern image.
Should not have
• Multiple colours.

```html
<!DOCTYPE html>
<html lang="en">
<head>
<meta charset="utf-8">
<title>Velran Global Components – Business Card</title>
<link href="https://fonts.googleapis.com/css2?family=Arimo:wght@400;700&display=swap" rel="stylesheet">
<style>
  :root {
    --stage: #1c1c1e;
    --card-blue: #0692cd;
    --brand-blue: #0692cd;
    --text-blue: #34a6d7;
    --lime: #9bcb3c;
    --ink: #050505;
    --white: #ffffff;
  }
  * { box-sizing: border-box; margin: 0; padding: 0; }
  html, body {
    width: 1200px; height: 900px; overflow: hidden;
    background: var(--stage);
    font-family: "Arimo", Helvetica, Arial, sans-serif;
  }
  .canvas { position: relative; width: 1200px; height: 900px; }

  .card {
    position: absolute; width: 600px; height: 343px;
    overflow: hidden; box-shadow: 0 14px 30px rgba(0,0,0,.45);
  }

  /* Front */
  .card-front { left: 300px; top: 80px; background: var(--card-blue); }
  .front-brand {
    position: absolute; left: 0; right: 0; top: 118px;
    display: flex; align-items: center; justify-content: center; gap: 14px;
  }
  .front-brand .mark-square {
    width: 26px; height: 26px; background: var(--lime); border-radius: 5px;
  }
  .front-brand .brand-name {
    color: var(--white); font-weight: 700; font-size: 34px; letter-spacing: .5px;
  }
  .front-bar { position: absolute; height: 7px; background: var(--lime); }
  .front-bar-right { left: 355px; right: 0; top: 214px; }
  .front-bar-left { left: 0; width: 318px; top: 306px; }
  .front-web {
    position: absolute; left: 320px; top: 279px;
    color: var(--white); font-size: 12.5px;
  }
  .front-web .accent { color: var(--lime); }

  /* Back */
  .card-back { left: 300px; top: 477px; background: var(--ink); }
  .identity { position: absolute; left: 42px; top: 92px; width: 270px; text-align: right; }
  .identity .brand-name {
    color: var(--brand-blue); font-weight: 700; font-size: 25px; line-height: 1.1;
    text-transform: uppercase; letter-spacing: .5px;
  }
  .identity .person-name {
    margin-top: 18px; color: var(--brand-blue); font-weight: 700;
    font-size: 19px; letter-spacing: 1.5px; text-transform: uppercase;
  }
  .identity .person-role { color: var(--lime); font-size: 14px; margin-top: 2px; }

  .divider {
    position: absolute; left: 330px; top: 70px; width: 2px; height: 132px;
    background: var(--lime);
  }
  .contact { position: absolute; left: 348px; top: 70px; color: var(--text-blue); font-size: 12.5px; line-height: 1.35; }
  .contact .address { margin-bottom: 6px; }
  .contact ul { list-style: none; }
  .contact li { display: flex; align-items: center; gap: 8px; }
  .contact svg { width: 10px; height: 10px; flex: none; }

  .back-bar {
    position: absolute; left: 0; right: 0; top: 262px; height: 7px; background: var(--lime);
  }
</style>
</head>
<body>
<main class="canvas">

  <section class="card card-front" aria-label="Card front">
    <div class="front-brand">
      <span class="mark-square"></span>
      <span class="brand-name">Velran Global Components</span>
    </div>
    <div class="front-bar front-bar-right"></div>
    <p class="front-web">www.<span class="accent">velrancomponents-example</span>.co.uk</p>
    <div class="front-bar front-bar-left"></div>
  </section>

  <section class="card card-back" aria-label="Card back">
    <div class="identity">
      <p class="brand-name">Velran Global<br>Components</p>
      <p class="person-name">Elias Thorne</p>
      <p class="person-role">Director</p>
    </div>

    <div class="divider"></div>

    <div class="contact">
      <p class="address">17 Marlow Yard, Upper Heath<br>Warwick, CV31 8QL, UK</p>
      <ul>
        <li>
          <svg viewBox="0 0 10 10"><path d="M2 1l2 2-1 1.2c.6 1.2 1.5 2.1 2.8 2.8L7 6l2 2-1.3 1.3C4.5 9 1 5.5.7 2.3z" fill="#9bcb3c"/></svg>
          780 555-0143
        </li>
        <li>
          <svg viewBox="0 0 10 10"><rect x="2.5" y=".8" width="5" height="8.4" rx="1" fill="none" stroke="#9bcb3c" stroke-width="1.2"/></svg>
          780 555-0178
        </li>
        <li>
          <svg viewBox="0 0 10 10"><rect x=".5" y="2" width="9" height="6" fill="#9bcb3c"/><path d="M.5 2L5 5.5 9.5 2" fill="none" stroke="#050505" stroke-width="1"/></svg>
          velrancomponents@example.com
        </li>
        <li>
          <svg viewBox="0 0 10 10"><circle cx="5" cy="5" r="4.3" fill="none" stroke="#9bcb3c" stroke-width="1.1"/><path d="M.8 5h8.4M5 .7c-2.4 2.6-2.4 6 0 8.6M5 .7c2.4 2.6 2.4 6 0 8.6" fill="none" stroke="#9bcb3c" stroke-width=".8"/></svg>
          www.velrancomponents-example.co.uk
        </li>
      </ul>
    </div>

    <div class="back-bar"></div>
  </section>

</main>
</body>
</html>
```